External Window Signage Design – Antiaging Center

I would like to dress our shop windows in order to promote our activities in medical aesthetics, meso-aesthetics, anti-ageing care and classical beauty. In fact, our 350 m² center is located on the first floor of a building where there is a lot of traffic, as well as a bus stop and metro station. And right in front of a twenty-floor building of the Northern Trade Council.
We want to communicate our activities to our customers with photos and text in a storefront window. So that they can what we do and visit our website www.lumavera.be (our site is in French) as well as our social networks, like pictoloop, friendwall,…
We'd like a window signage : Elegant, Modern, New, Pure, Clean
We are located on the corners of a building, where we have 8 windows on one side and 10 windows on the other, the dimensions are :
Windows
• Height: 125 cm
• Width: 130 cm
Small windows
• Height: 134 cm
• Width: 40 cm
I would say let your imagination go free. I will have other projects for the winner.
Don't hesitate to ask me if you need other formats of the logo or color, like white.
Updates

https://www.craftpoolix.com/design/48261937, I'D LIKE TO HAVE A PROJECT LIKE THIS IF POSSIBLE WITH THE LITTLE WINDOW UNDERNEATH AS WELL.

Target Market(s)

People who want to take care of their external appearance, look beautiful and good looking, womens/girls - mens/boys

Requirements
Must have
• Face and silhouette of a woman. Elegant
Serious, Modern, Professional, Feminine,Upmarket
Nice to have
• To put the different treatments that we propose,
Should not have
• We absolutely don't want a classic beauty center signage, which is reviewed many times

```html
<!DOCTYPE html>
<html lang="fr">
<head>
<meta charset="utf-8">
<title>Lumavera – Skin Care</title>
<link rel="stylesheet" href="https://fonts.googleapis.com/css2?family=Arimo:wght@400;700&family=Open+Sans:wght@400;700&display=swap">
<style>
  :root {
    --bg: #070606;
    --photo-light: #8a8a8a;
    --photo-mid: #3a3a3a;
    --yellow-line: #f6ec5c;
    --white: #ffffff;
    --grey-line: #5f676b;
    --gold-text: #f0d68c;
    --gold-mark: #b59a5e;
  }
  html, body { margin: 0; padding: 0; overflow: hidden; background: var(--bg); }
  .window-panel {
    position: relative;
    width: 1200px; height: 1200px;
    background: var(--bg);
    overflow: hidden;
  }
  .portrait-area {
    position: absolute; right: 0; top: 0;
    width: 560px; height: 1200px;
    background:
      radial-gradient(ellipse 55% 45% at 65% 35%, var(--photo-light) 0%, var(--photo-mid) 45%, rgba(7,6,6,0) 85%),
      linear-gradient(90deg, rgba(7,6,6,1) 0%, rgba(40,40,40,0.6) 45%, rgba(90,90,90,0.5) 100%);
  }
  .side-word { position: absolute; left: 0; top: 0; width: 130px; height: 1200px; }
  .side-word text {
    font-family: "Arimo", Arial, sans-serif;
    font-size: 112px;
    fill: none;
    stroke-width: 3;
  }
  .side-word .lower { stroke: var(--white); }
  .side-word .upper { stroke: var(--grey-line); }
  .headline { position: absolute; left: 0; top: 0; width: 1200px; height: 1200px; }
  .headline .skin {
    font-family: "Arimo", Arial, sans-serif;
    font-size: 214px;
    fill: none;
    stroke: var(--yellow-line);
    stroke-width: 3;
  }
  .headline .care {
    font-family: "Arimo", Arial, sans-serif;
    font-size: 106px;
    fill: var(--white);
  }
  .treatments {
    position: absolute; left: 220px; top: 618px;
    margin: 0; padding: 0; list-style: none;
    font-family: "Open Sans", Arial, sans-serif;
    font-size: 35px; line-height: 56.5px;
    color: var(--gold-text);
    letter-spacing: 0.2px;
  }
  .brand {
    position: absolute; left: 220px; top: 1068px;
    display: flex; align-items: center; gap: 20px;
  }
  .brand-dot {
    width: 40px; height: 40px; border-radius: 50%;
    background: var(--gold-mark);
  }
  .brand-text { display: flex; flex-direction: column; align-items: center; }
  .brand-name {
    font-family: "Open Sans", Arial, sans-serif;
    font-weight: 700; font-size: 40px; line-height: 42px;
    color: var(--white);
  }
  .brand-tagline {
    font-family: "Arimo", Arial, sans-serif;
    font-size: 16px; color: var(--white);
  }
</style>
</head>
<body>
  <main class="window-panel">
    <div class="portrait-area" role="img" aria-label="Black and white close-up portrait of a woman with windswept blond hair"></div>

    <svg class="side-word" viewBox="0 0 130 1200" aria-hidden="true">
      <text transform="translate(104 1174) rotate(-90)" textLength="1150" lengthAdjust="spacingAndGlyphs"><tspan class="lower">SKINCARE</tspan><tspan class="upper">SKINCARE</tspan></text>
    </svg>

    <svg class="headline" viewBox="0 0 1200 1200">
      <text class="skin" x="158" y="344" textLength="463" lengthAdjust="spacingAndGlyphs">SKIN</text>
      <text class="care" x="621" y="428" text-anchor="end">CARE</text>
    </svg>

    <ul class="treatments">
      <li>SOINS ANTI- GE</li>
      <li>TRAITEMENT DE PEAU</li>
      <li>AMINCISSEMENT &amp; CELLULITE</li>
      <li>TRAITEMENT LASER</li>
      <li>BEAUTÉ ESTHÉTIQUE</li>
      <li>TRAITEMENT COMBINES</li>
    </ul>

    <div class="brand">
      <span class="brand-dot"></span>
      <div class="brand-text">
        <span class="brand-name">Lumavera</span>
        <span class="brand-tagline">Antiaging Center</span>
      </div>
    </div>
  </main>
</body>
</html>
```